Breakfast Cafe - The Sunny Nook

It is for my breakfast and lunch cafe with a hawaiian / beach theme. I am open 7 days a week from 7am to 2pm. We serve traditional American food such as omelettes, pancakes, burgers and sandwiches. I'll upload my old card and my new logo to be used. We have a lot of day to day regulars who eat there during the week, our t-shirts actually say 'Locals Only' on them. Hope this helps. Thanks.

Target Market(s)

anyone who has an appetite!

Industry/Entity Type

American Restaurant

Contact Information for Business Card

4815C Marlow Grove Avenue
Long Beach, California
(555) 731-2294

Requirements
Must have
• Address and phone number easily readable.
Nice to have
• beach or tropical theme

```html
<!DOCTYPE html>
<html lang="en">
<head>
<meta charset="utf-8">
<title>The Sunny Nook – Business Card</title>
<link href="https://fonts.googleapis.com/css2?family=Lato:wght@400;700;900&display=swap" rel="stylesheet">
<style>
  :root {
    --orange: #b5620f;
    --sky: #5bc0d6;
    --ink: #1c1c1c;
    --paper: #ffffff;
    --backdrop: #3a3a3c;
  }
  * { margin: 0; padding: 0; box-sizing: border-box; }
  html, body { width: 1200px; height: 782px; overflow: hidden; }
  body {
    background: var(--backdrop);
    font-family: "Lato", Arial, sans-serif;
    position: relative;
  }
  .card {
    position: absolute;
    top: 236px;
    width: 540px;
    height: 310px;
    overflow: hidden;
    box-shadow: 0 10px 24px rgba(0,0,0,0.35);
  }

  /* Front: contact side */
  .card-front { left: 40px; background: var(--paper); }
  .front-art { position: absolute; inset: 0; width: 100%; height: 100%; }
  .tagline {
    position: absolute; left: 74px; top: 28px;
    color: var(--orange); font-size: 24px; font-weight: 400;
  }
  .front-body {
    position: absolute; left: 40px; right: 24px; top: 86px;
    display: flex; justify-content: space-between; align-items: flex-start;
    gap: 20px;
  }
  .contact {
    color: var(--ink); font-size: 17px; line-height: 1.25;
    white-space: nowrap;
  }
  .contact .phone { display: flex; align-items: center; gap: 6px; }
  .phone-icon { width: 20px; height: 20px; flex: none; }
  .front-name {
    margin-top: 24px; text-align: center; white-space: nowrap;
    color: var(--sky); font-weight: 900; font-size: 28px; line-height: 1;
  }
  .front-name .city {
    display: block; font-size: 12px; letter-spacing: 4px; margin-top: 6px;
  }
  .hours {
    position: absolute; left: 40px; top: 204px;
    color: var(--orange); font-size: 23px;
  }

  /* Back: brand side */
  .card-back {
    left: 620px; background: var(--orange);
    display: flex; flex-direction: column; align-items: center;
  }
  .brand-mark {
    margin-top: 40px; width: 120px; height: 120px; border-radius: 50%;
    background: var(--paper); opacity: 0.9;
  }
  .brand-name {
    margin-top: 16px; color: var(--sky);
    font-weight: 900; font-size: 38px; line-height: 1;
  }
  .brand-city {
    margin-top: 4px; color: var(--sky); font-weight: 900;
    font-size: 13px; letter-spacing: 5px;
  }
  .menu-line {
    margin-top: 26px; color: var(--sky); font-size: 20px;
  }
</style>
</head>
<body>

  <section class="card card-front">
    <svg class="front-art" viewBox="0 0 540 310" preserveAspectRatio="none" aria-hidden="true">
      <polygon points="0,0 50,0 28,34 0,34" fill="var(--orange)"/>
      <polygon points="50,0 50,34 28,34" fill="var(--sky)"/>
      <polygon points="0,280 250,280 236,310 0,310" fill="var(--orange)"/>
      <polygon points="250,280 540,280 540,310 236,310" fill="var(--sky)"/>
    </svg>

    <p class="tagline">Family owned and operated!</p>

    <div class="front-body">
      <div class="contact">
        <p class="phone">
          <svg class="phone-icon" viewBox="0 0 24 24" aria-hidden="true">
            <rect width="24" height="24" rx="3" fill="var(--orange)"/>
            <path d="M8 5.5l2 3-1.3 1.3c.8 1.8 2.2 3.2 4 4L14 12.5l3 2-1 2.5c-4.6-.3-9.3-5-9.5-9.5z" fill="#fff"/>
          </svg>
          (555) 731-2294
        </p>
        <p>4815C Marlow Grove Avenue</p>
        <p>Long Beach, California</p>
      </div>
      <p class="front-name">The Sunny Nook<span class="city">LONG BEACH, CA</span></p>
    </div>

    <p class="hours">Breakfast &amp; Lunch 7am - 2pm Daily</p>
  </section>

  <section class="card card-back">
    <div class="brand-mark"></div>
    <p class="brand-name">The Sunny Nook</p>
    <p class="brand-city">LONG BEACH, CA</p>
    <p class="menu-line">Omelettes | Pancakes | Burgers | Sandwiches</p>
  </section>

</body>
</html>
```